Custom unique Stationary design for Logistics company

We need a custom, unique , elegant and luxurious full stationary design using our new logo, following these guidelines:
1- Business card: double sided, both sides uses the navy blue as the background main color (same as the code of the navy blue used in our logo).
2- envelope and folder: also use the same navy blue as the main background color.
3- book cover( notepad cover) : same thing with the navy blue
4- letterhead: feel free to use the combination of the colors in our logo.
5- rest of the items are up to your creativity

Target Market(s)

corporates and other businesses

Industry/Entity Type

Logistics and heavy machines contractors

Requirements
Must have
• Letterhead, business card, envelope, notepad cover, paper, file
Nice to have
• navy blue to be main background color for business card, envelope, notepad cover

```html
<!DOCTYPE html>
<html lang="en">
<head>
<meta charset="utf-8">
<title>Northbay Freight Group – Envelope</title>
<link href="https://fonts.googleapis.com/css2?family=Montserrat:wght@400;800&display=swap" rel="stylesheet">
<style>
  :root {
    --navy: #064d70;
    --orange: #e65a2e;
    --paper: #f4f3f3;
    --ink: #1a1a1a;
    --backdrop: #d2d1d1;
  }
  * { margin: 0; padding: 0; box-sizing: border-box; }
  html, body {
    width: 1200px; height: 1050px; overflow: hidden;
    background: var(--backdrop);
    font-family: "Montserrat", sans-serif;
  }
  .canvas { position: relative; width: 1200px; height: 1050px; }
  .envelope {
    position: absolute; left: 145px; width: 910px; height: 390px;
    background: var(--paper); overflow: hidden;
  }
  .envelope--back { top: 105px; }
  .envelope--front { top: 556px; }
  .envelope svg { position: absolute; inset: 0; }
  .flap-name {
    position: absolute; top: 62px; left: 0; width: 100%;
    text-align: center; color: #fff;
    font-weight: 800; font-size: 26px; letter-spacing: 1px;
  }
  .return-name {
    position: absolute; left: 42px; top: 82px;
    color: var(--navy); font-weight: 800; font-size: 30px; letter-spacing: 0.5px;
  }
  .return-address {
    position: absolute; left: 41px; top: 188px;
    color: var(--ink); font-weight: 400; font-size: 15.5px; line-height: 20px;
    font-style: normal;
  }
</style>
</head>
<body>
<main class="canvas">
  <section class="envelope envelope--back" aria-label="Envelope back">
    <svg width="910" height="390" viewBox="0 0 910 390" aria-hidden="true">
      <path class="flap" fill="var(--navy)"
        d="M0,0 H910 L884,88 Q872,128 830,130 H80 Q38,128 26,88 Z"/>
    </svg>
    <div class="flap-name">NORTHBAY FREIGHT GROUP</div>
  </section>

  <section class="envelope envelope--front" aria-label="Envelope front">
    <svg width="910" height="390" viewBox="0 0 910 390" aria-hidden="true">
      <path class="swoop-accent" fill="var(--orange)"
        d="M28,271 Q448,397 868,275 Q448,421 28,271 Z"/>
      <path class="swoop-band" fill="var(--navy)"
        d="M0,270 Q455,440 910,270 V390 H0 Z"/>
    </svg>
    <div class="return-name">NORTHBAY FREIGHT GROUP</div>
    <address class="return-address">
      418 Calder Park RD, Unit 110<br>
      Oakridge, ON K7P&nbsp; 3M4
    </address>
  </section>
</main>
</body>
</html>
```